Convention display re-design- six destination banners for tour company

We travel to conventions to promote our group travel business. We set up six banners all in a row that are each 36" x 84". The current display advertises six cities and the price for each. This design is getting tired and needs updating. We like big destination imagery, printed pricing and a horizontal design element that connects all the banners into one visually cohesive unit. The attached photos are of our current display. Please modernize this. The other attachments are poster dimensions. Send designs of the whole piece (as opposed to just one banner). Thank you!!
Target Market(s)
Teachers that travel with their students
Industry/Entity Type
Business
Font styles to use
Other font styles liked:
- See logo
Requirements
Must have
- Logo, featured cities with prices, horizontal connecting elements across the six banners. Clean, modern design.
Nice to have
- Big beautiful photos of the cities. A design theme that can be re-used on other print materials like itineraries and business cards so they look like they all go together.
Should not have
- Nothing cheesy.

```html
<!DOCTYPE html>
<html lang="en">
<head>
<meta charset="utf-8">
<title>Clearway Group Tours – Convention Banner Wall</title>
<link rel="stylesheet" href="https://fonts.googleapis.com/css2?family=Nunito:wght@800&family=Oswald:wght@500&family=Merriweather:wght@400&display=swap">
<style>
  :root {
    --page: #e6e6e6;
    --white: #ffffff;
    --green-dark: #1f6e33;
    --green-mid: #3f8f3a;
    --green-light: #8dc63f;
    --green-text: #3e8a36;
    --sky-top: #3f72b8;
    --sky-bottom: #8fb3dc;
    --price-red: #e3262b;
    --price-yellow: #f6e11a;
  }
  * { box-sizing: border-box; margin: 0; padding: 0; }
  html, body {
    width: 1200px; height: 835px; overflow: hidden;
    background: var(--page);
  }
  .banner-wall {
    position: absolute; left: 0; top: 183px;
    width: 1200px; height: 469px; overflow: hidden;
    background: var(--white);
  }
  .banner {
    position: absolute; top: 0; width: 200px; height: 469px;
  }
  .banner--sky { background: linear-gradient(180deg, var(--sky-top) 20%, var(--sky-bottom) 80%); }
  .banner--light { background: linear-gradient(180deg, #ffffff 30%, #e7edf3 80%); }
  .scene {
    position: absolute; left: 0; width: 200px; bottom: 40px;
  }
  .wave-layer { position: absolute; inset: 0; }
  .brand {
    position: absolute; top: 26px; width: 200px;
    display: flex; align-items: center; justify-content: center; gap: 6px;
    font-family: "Merriweather", Georgia, serif; font-weight: 400;
    font-size: 14px; color: var(--green-mid); letter-spacing: 0.3px;
    white-space: nowrap;
  }
  .brand__dot {
    width: 9px; height: 9px; border-radius: 50%; background: var(--green-light); flex: none;
  }
  .city {
    position: absolute; width: 200px; text-align: center;
    font-family: "Nunito", "Arial Rounded MT Bold", sans-serif; font-weight: 800;
    font-size: 33px; line-height: 31px;
  }
  .city--green { color: var(--green-text); }
  .city--white { color: var(--white); }
  .deal {
    position: absolute; transform: rotate(-12deg); transform-origin: left top;
    font-family: "Oswald", "Arial Narrow", sans-serif; font-weight: 500;
    line-height: 1; white-space: nowrap;
  }
  .deal__price { display: block; font-size: 46px; letter-spacing: -0.5px; line-height: 1.05; }
  .deal__note { display: block; font-size: 15px; margin-left: 10px; margin-top: 4px; }
  .deal--red { color: var(--price-red); }
  .deal--yellow { color: var(--price-yellow); }
</style>
</head>
<body>
<main class="banner-wall">
  <section class="banner banner--light" style="left:0">
    <div class="scene" role="img" aria-label="Photo of the Golden Gate Bridge" style="top:200px;background:linear-gradient(180deg,rgba(255,255,255,0),#c9463d 45%,#6e5a55)"></div>
  </section>
  <section class="banner banner--sky" style="left:200px">
    <div class="scene" role="img" aria-label="Photo of Navy Pier with its Ferris wheel and tour boats" style="top:270px;background:linear-gradient(180deg,rgba(143,179,220,0),#c5cdd8 40%,#4f7c93)"></div>
  </section>
  <section class="banner banner--light" style="left:400px">
    <div class="scene" role="img" aria-label="Photo of a marble monument and the Capitol dome" style="top:150px;background:linear-gradient(180deg,rgba(255,255,255,0),#b9bdc4 35%,#d7d7d7)"></div>
  </section>
  <section class="banner banner--sky" style="left:600px">
    <div class="scene" role="img" aria-label="Photo of the Statue of Liberty" style="top:140px;background:linear-gradient(180deg,rgba(143,179,220,0),#7f9c93 45%,#4d5652)"></div>
  </section>
  <section class="banner banner--light" style="left:800px">
    <div class="scene" role="img" aria-label="Photo of an ornate golden building facade" style="top:270px;background:linear-gradient(180deg,rgba(255,255,255,0),#d6a23a 40%,#9a5a22)"></div>
  </section>
  <section class="banner banner--sky" style="left:1000px">
    <div class="scene" role="img" aria-label="Aerial photo of the New Orleans skyline and stadium" style="top:260px;background:linear-gradient(180deg,rgba(143,179,220,0),#8d949c 35%,#5c6670)"></div>
  </section>

  <svg class="wave-layer" viewBox="0 0 1200 469" width="1200" height="469" aria-hidden="true">
    <defs>
      <linearGradient id="edge-shade" x1="0" x2="1">
        <stop offset="0.55" stop-color="#ffffff"/>
        <stop offset="1" stop-color="#3f8f3a"/>
      </linearGradient>
      <linearGradient id="ground" x1="0" y1="0" x2="0" y2="1">
        <stop offset="0" stop-color="#98cc3c"/>
        <stop offset="1" stop-color="#3d8b3d"/>
      </linearGradient>
      <clipPath id="top-band">
        <path d="M0 0 H1200 V72 C1060 75 960 130 860 130 C760 130 690 66 560 66 C440 66 320 120 220 125 C140 128 80 88 0 84 Z"/>
      </clipPath>
    </defs>
    <g clip-path="url(#top-band)">
      <rect x="0" y="0" width="200" height="140" fill="url(#edge-shade)"/>
      <rect x="200" y="0" width="200" height="140" fill="url(#edge-shade)"/>
      <rect x="400" y="0" width="200" height="140" fill="url(#edge-shade)"/>
      <rect x="600" y="0" width="200" height="140" fill="url(#edge-shade)"/>
      <rect x="800" y="0" width="200" height="140" fill="url(#edge-shade)"/>
      <rect x="1000" y="0" width="200" height="140" fill="url(#edge-shade)"/>
    </g>
    <path d="M0 84 C80 88 140 128 220 125 C320 120 440 66 560 66 C690 66 760 130 860 130 C960 130 1060 75 1200 72" fill="none" stroke="var(--green-dark)" stroke-width="5"/>
    <path d="M0 398 C120 396 190 358 320 356 C460 354 540 412 640 412 C740 412 800 358 920 356 C1040 354 1120 398 1200 400 L1200 469 L0 469 Z" fill="url(#ground)"/>
    <g fill="none" stroke="#ffffff" stroke-linecap="round">
      <path d="M0 418 C80 416 150 410 210 400" stroke-width="5"/>
      <path d="M0 430 C90 428 170 420 230 408" stroke-width="3"/>
      <path d="M280 378 C380 372 520 410 640 432 C720 446 790 430 820 420" stroke-width="5"/>
      <path d="M300 392 C400 386 530 424 650 444" stroke-width="3"/>
      <path d="M700 430 C800 420 880 380 980 376 C1060 374 1120 396 1200 408" stroke-width="5"/>
      <path d="M1060 410 C1120 412 1160 416 1200 420" stroke-width="3"/>
    </g>
  </svg>

  <div class="brand" style="left:0"><span class="brand__dot"></span>Clearway group tours</div>
  <div class="brand" style="left:200px"><span class="brand__dot"></span>Clearway group tours</div>
  <div class="brand" style="left:400px"><span class="brand__dot"></span>Clearway group tours</div>
  <div class="brand" style="left:600px"><span class="brand__dot"></span>Clearway group tours</div>
  <div class="brand" style="left:800px"><span class="brand__dot"></span>Clearway group tours</div>
  <div class="brand" style="left:1000px"><span class="brand__dot"></span>Clearway group tours</div>

  <h2 class="city city--green" style="left:2px;top:112px">San<br>Francisco</h2>
  <h2 class="city city--white" style="left:200px;top:134px">Chicago</h2>
  <h2 class="city city--green" style="left:402px;top:128px;font-size:28px;line-height:28px">Washington<br>DC</h2>
  <h2 class="city city--white" style="left:635px;top:145px">New<br>York</h2>
  <h2 class="city city--green" style="left:800px;top:150px">San<br>Antonio</h2>
  <h2 class="city city--white" style="left:1008px;top:110px">New<br>Orleans</h2>

  <p class="deal deal--red" style="left:10px;top:208px"><span class="deal__price">$414</span><span class="deal__note">ALL INCLUSIVE</span></p>
  <p class="deal deal--yellow" style="left:218px;top:210px"><span class="deal__price" style="font-size:40px">$497</span><span class="deal__note" style="font-size:13px">ALL INCLUSIVE</span></p>
  <p class="deal deal--red" style="left:478px;top:212px"><span class="deal__price">$374</span><span class="deal__note">ALL INCLUSIVE</span></p>
  <p class="deal deal--yellow" style="left:675px;top:240px"><span class="deal__price">$520</span><span class="deal__note">ALL INCLUSIVE</span></p>
  <p class="deal deal--red" style="left:855px;top:248px"><span class="deal__price">$311</span><span class="deal__note">ALL INCLUSIVE</span></p>
  <p class="deal deal--yellow" style="left:1050px;top:208px"><span class="deal__price">$435</span><span class="deal__note">ALL INCLUSIVE</span></p>
</main>
</body>
</html>
```